Business Card for Dental Office - "online review card"

I would like to develop a tasteful card (that would compliment my existing business card) that provides my patients a written link to a portal on my website that would facilitate the generation of online reviews.

My existing business card was a Lumaquarry project a few years ago and has been well received. I hope that it is easily accessed online for reference.

Target Market(s)

Existing patients who need guidance in accessing the "write a review" section of my website

Industry/Entity Type

Business

Requirements
Must have
• -a similar look to my existing card:
http://www.lumaquarry.com.au/contest.aspx?id=5192&page=3

-a link to the following url in writing:
http://www.tessaroldental.com/reviews.html

- a reference to "appreciating feedback" or "how are we doing?"

```html
<!DOCTYPE html>
<html lang="en">
<head>
<meta charset="utf-8">
<title>Tessarol Dental – Review Card</title>
<link rel="stylesheet" href="https://fonts.googleapis.com/css2?family=Montserrat:wght@400&family=Open+Sans:wght@400;700&display=swap">
<style>
  :root {
    --page: #e6e6e6;
    --card: #ffffff;
    --card-edge: #5a5a5a;
    --brand-blue: #2f2c84;
    --brand-blue-deep: #27246f;
    --name-grey: #5b5b5b;
    --tag-grey: #7a7a7a;
    --on-blue: #ffffff;
  }
  * { margin: 0; padding: 0; box-sizing: border-box; }
  html, body {
    width: 1200px; height: 711px; overflow: hidden;
    background: var(--page);
  }
  .canvas { position: relative; width: 1200px; height: 711px; }
  .card {
    position: absolute; width: 514px; height: 294px;
    background: var(--card);
    border: 1px solid var(--card-edge);
    border-radius: 10px; overflow: hidden;
  }
  .card--review { left: 57px; top: 41px; }
  .card--front { left: 57px; top: 370px; }
  .card--plain { left: 607px; top: 208px; }

  .review-band { position: absolute; inset: 0; }

  .brand-square {
    position: absolute; background: var(--brand-blue);
    border-radius: 10px;
  }
  .brand-name {
    position: absolute; white-space: nowrap;
    font-family: "Montserrat", sans-serif; font-weight: 400;
    color: var(--name-grey); letter-spacing: -0.2px;
  }
  .brand-tag {
    position: absolute; white-space: nowrap;
    font-family: "Montserrat", sans-serif; font-weight: 400;
    color: var(--tag-grey); text-transform: uppercase;
  }

  /* review card */
  .card--review .brand-square { left: 65px; top: 55px; width: 80px; height: 80px; }
  .card--review .brand-name { left: 168px; top: 56px; font-size: 23px; }
  .card--review .brand-tag { left: 312px; top: 88px; font-size: 9px; letter-spacing: 2.6px; }
  .review-heading {
    position: absolute; left: 25px; top: 226px;
    font-family: "Open Sans", sans-serif; font-weight: 400;
    font-size: 16px; color: var(--on-blue); letter-spacing: 0.2px;
  }
  .review-link {
    position: absolute; left: 25px; top: 258px;
    font-family: "Open Sans", sans-serif; font-weight: 700;
    font-size: 16.5px; color: var(--on-blue); text-decoration: none;
  }

  /* front card */
  .card--front .brand-square { left: 172px; top: 40px; width: 172px; height: 172px; border-radius: 24px; }
  .card--front .brand-name { left: 0; width: 100%; text-align: center; top: 224px; font-size: 16px; }
  .card--front .brand-tag { left: 0; width: 100%; text-align: center; top: 248px; font-size: 6px; letter-spacing: 1.6px; }

  /* plain card */
  .card--plain .brand-square { left: 36px; top: 98px; width: 92px; height: 92px; border-radius: 12px; }
  .card--plain .brand-name { left: 156px; top: 100px; font-size: 26px; }
  .card--plain .brand-tag { left: 318px; top: 136px; font-size: 10px; letter-spacing: 3px; }
</style>
</head>
<body>
<main class="canvas">

  <section class="card card--review" aria-label="Review card">
    <svg class="review-band" viewBox="0 0 514 294" width="514" height="294" aria-hidden="true">
      <defs>
        <linearGradient id="bandFill" x1="0" y1="0" x2="1" y2="0">
          <stop offset="0" stop-color="var(--brand-blue-deep)"/>
          <stop offset="1" stop-color="var(--brand-blue)"/>
        </linearGradient>
      </defs>
      <path d="M0,178 L514,178 L514,294 L0,294 Z" fill="url(#bandFill)"/>
    </svg>
    <div class="brand-square"></div>
    <p class="brand-name">Adrian M. Tessarol, DDS</p>
    <p class="brand-tag">And Associates</p>
    <p class="review-heading">APPRECIATING FEEDBACK</p>
    <a class="review-link" href="http://www.tessaroldental.com/reviews.html">http://www.tessaroldental.com/reviews.html</a>
  </section>

  <section class="card card--front" aria-label="Business card front">
    <div class="brand-square"></div>
    <p class="brand-name">Adrian M. Tessarol, DDS</p>
    <p class="brand-tag">Family and Cosmetic Dentistry</p>
  </section>

  <section class="card card--plain" aria-label="Business card back">
    <div class="brand-square"></div>
    <p class="brand-name">Adrian M. Tessarol, DDS</p>
    <p class="brand-tag">And Associates</p>
  </section>

</main>
</body>
</html>
```